4th Generation Family Business Needs a New Card Design!

We are a family owned 4th Generation company. We are based in the Sydney, Australia area and we are desperately in need of a more modern and classy card. We are monumental masons who design, supply & erect lasting memorials throughout cemeteries in Sydney. Our customers are normally in a period of grieving. I have attached logo files that will need to be implemented on the card. Company was established 1935. Australian Owned and Operated. Card needs to be designed to PIXO.com specification.

Target Market(s)

Our target market is based upon people that a grieving for family members that have passed away. We also deal with alot of companies that own and operate cemeteries.

Industry/Entity Type

Business

Contact Information for Business Card

Simon Harcourt, Operations Manager, 0417293086, simon@harcourtmemorials.com.au
Lewis Harcourt, Director, 0491630572, lewis@harcourtmemorials.com.au
Phone # 02 9561 3048
Website: www.harcourtmemorials.com.au
Address: Suite 17, 8 Palfrey Lane, West Carlow, Sydney NSW 2156

Font styles to use
Serif
Decorative
Script

Requirements
Must have
• Would like to see the logo nicely implemented with a modern design. Embossed lettering would be a nice additive.

```html
<!DOCTYPE html>
<html lang="en">
<head>
<meta charset="utf-8">
<title>Harcourt Memorials – Business Card</title>
<link rel="stylesheet" href="https://fonts.googleapis.com/css2?family=Cinzel:wght@500;600&family=Open+Sans:wght@400&display=swap">
<style>
  :root {
    --backdrop: #e9e6e1;
    --card: #f6f5f1;
    --ink: #1d1c1a;
    --ink-soft: #2c2b28;
    --gold: #e8b923;
    --shadow: rgba(40, 30, 20, 0.18);
  }
  * { margin: 0; padding: 0; box-sizing: border-box; }
  html, body {
    width: 909px;
    height: 1200px;
    overflow: hidden;
    background: var(--backdrop);
  }
  .sheet {
    width: 909px;
    height: 1200px;
    display: flex;
    flex-direction: column;
    align-items: center;
    justify-content: center;
    gap: 80px;
  }
  .card {
    width: 720px;
    height: 440px;
    background: var(--card);
    box-shadow: 0 10px 28px var(--shadow), 0 2px 4px var(--shadow);
    position: relative;
  }
  .card--front {
    display: flex;
    align-items: center;
    justify-content: center;
  }
  .wordmark {
    font-family: "Cinzel", serif;
    font-weight: 600;
    color: var(--ink);
    text-align: center;
    line-height: 1.05;
    display: flex;
    align-items: center;
    gap: 14px;
  }
  .wordmark__square {
    width: 16px;
    height: 16px;
    background: var(--ink);
    flex: none;
  }
  .wordmark__name {
    font-size: 40px;
    letter-spacing: 2px;
  }
  .card--front .wordmark__name { font-size: 46px; }

  .card--back {
    display: flex;
    align-items: center;
    padding: 0 48px 0 56px;
    gap: 40px;
  }
  .card--back .brand {
    flex: 0 0 300px;
    display: flex;
    flex-direction: column;
    align-items: center;
    gap: 14px;
  }
  .card--back .wordmark__name { font-size: 34px; }
  .brand__rule {
    width: 240px;
    height: 3px;
    background: var(--gold);
  }
  .details {
    flex: 1;
    font-family: "Open Sans", sans-serif;
    color: var(--ink-soft);
    font-size: 15px;
    line-height: 1.5;
  }
  .details__name {
    font-family: "Cinzel", serif;
    font-weight: 600;
    font-size: 24px;
    color: var(--ink);
    line-height: 1.1;
  }
  .details__role {
    font-family: "Cinzel", serif;
    font-weight: 500;
    font-size: 17px;
    letter-spacing: 1px;
    color: var(--ink);
    margin-bottom: 12px;
  }
  .details__block { margin-bottom: 10px; }
</style>
</head>
<body>
  <main class="sheet">
    <section class="card card--front" aria-label="Card front">
      <div class="wordmark">
        <span class="wordmark__square" aria-hidden="true"></span>
        <span class="wordmark__name">Harcourt Memorials</span>
      </div>
    </section>

    <section class="card card--back" aria-label="Card back">
      <div class="brand">
        <div class="wordmark">
          <span class="wordmark__name">Harcourt<br>Memorials</span>
        </div>
        <div class="brand__rule" aria-hidden="true"></div>
      </div>
      <div class="details">
        <p class="details__name">Simon Harcourt</p>
        <p class="details__role">Operations Manager</p>
        <div class="details__block">
          <p>Suite 17, 8 Palfrey Lane</p>
          <p>West Carlow, Sydney NSW 2156</p>
        </div>
        <div class="details__block">
          <p>0417293086 (Mobile)</p>
          <p>02 9561 3048 (Phone)</p>
        </div>
        <p>simon@harcourtmemorials.com.au</p>
        <p>www.harcourtmemorials.com.au</p>
      </div>
    </section>
  </main>
</body>
</html>
```